Copperleaf Balustrade Website Redesign

I want a fresh new design for my website. Original website
www.copperleafbalustrade-example.com. Will need to add additional photos for winning designer. Please use the basic layout for new design. Looking to get a more modern, functional site to attract new customer and ne bale to highlight past projects. Need it to be easy to navigate and get in touch with me for inquiries.

Target Market(s)

Builders and home owners in WA state

Industry/Entity Type

Building, Construction, Deck building

Coding

Coded - Design and coding required

Number of Pages Required

5+ page

Font styles to use
Sans Serif

Colors
0054AA
0677BA
7BADD7
CADEEF
E8F1F8
0094D4
00A9DD
6FCCEA
C7EBF8
E9F6FB
00AB8E
00BBA5
67D7C9
C6EFE9
E9F9F6
59FF00
82FF00
B8FF75
E3FFCB
F4FFEA

Requirements
Must have
• Will need to add more photos of completed projects
Nice to have
• Fresh take on old website, something modern
Should not have
• Nothing comes to mind

```html
<!DOCTYPE html>
<html lang="en">
<head>
<meta charset="utf-8">
<title>Copperleaf Balustrade</title>
<link href="https://fonts.googleapis.com/css2?family=Archivo:wght@500;600;700;800&family=Jost:wght@400;500;600&display=swap" rel="stylesheet">
<style>
:root{
  --primary:#0054AA;
  --primary-dark:#003f80;
  --blue:#0677BA;
  --sky:#0094D4;
  --teal:#00AB8E;
  --teal-light:#67D7C9;
  --cyan-light:#6FCCEA;
  --lime:#59FF00;
  --ink:#1d1d1d;
  --muted:#3a3a3a;
  --mint:#E9F6FB;
  --line:#CADEEF;
  --white:#ffffff;
  --footer:#0b1f3a;
}
*{box-sizing:border-box;margin:0;padding:0}
html,body{width:1200px;height:4471px;overflow:hidden}
body{font-family:"Jost",sans-serif;color:var(--ink);background:var(--white);position:relative}
h1,h2,h3,.btn,.nav a{font-family:"Archivo",sans-serif}
.ph{position:absolute;inset:0}

/* header */
.site-header{height:90px;position:relative}
.brand{position:absolute;left:57px;top:22px;display:flex;align-items:center;gap:12px}
.brand-mark{width:40px;height:40px;background:var(--primary)}
.brand-name{font-family:"Archivo",sans-serif;font-weight:600;font-size:21px;line-height:23px;color:var(--primary);letter-spacing:.5px}
.nav{position:absolute;right:57px;top:30px;display:flex;gap:38px;align-items:center}
.nav a{font-size:14px;font-weight:600;color:var(--ink);text-decoration:none}
.nav a.active{color:var(--primary)}
.nav a.cta{background:var(--primary);color:#fff;padding:9px 16px}

/* hero */
.hero{height:504px;position:relative;color:#fff}
.hero .ph{background:linear-gradient(180deg,#2f4658 0%,#8a7a5e 40%,#c89a55 52%,#3c5230 75%,#1d2a18 100%)}
.hero-content{position:absolute;left:57px;top:190px;width:720px}
.hero h1{font-size:37px;line-height:46px;font-weight:700;text-transform:uppercase}
.hero p{font-size:12px;line-height:18px;margin-top:12px;font-weight:500;width:540px}
.hero .actions{margin-top:22px;display:flex;gap:14px}
.btn{display:inline-block;font-size:13px;font-weight:600;padding:9px 15px;text-decoration:none;text-transform:uppercase}
.btn-solid{background:var(--primary);color:#fff;border:2px solid var(--primary)}
.btn-ghost{border:2px solid #fff;color:#fff}
.btn-outline{border:1.5px solid var(--ink);color:var(--ink);background:#fff}
.hero-next{position:absolute;right:57px;top:322px;width:46px;height:46px;border-radius:50%;background:rgba(255,255,255,.25);display:flex;align-items:center;justify-content:center}

/* about */
.about{height:451px;position:relative}
.about-photo{position:absolute;left:57px;top:52px;width:503px;height:346px;background:linear-gradient(180deg,#b9c8d6 0%,#7d8a73 45%,#4b5a3d 70%,#8c8c88 100%)}
.about-text{position:absolute;left:622px;top:68px;width:520px}
.section-title{font-size:25px;font-weight:700;color:var(--primary);text-transform:uppercase}
.about-text p{font-size:12.5px;line-height:20px;color:var(--muted);margin-top:14px}
.about-text .btn{margin-top:18px}

/* products */
.products{height:671px;position:relative;color:#fff}
.products .ph{background:linear-gradient(180deg,#1f2a1c 0%,#2e3b24 50%,#151c12 100%)}
.products-head{position:absolute;left:57px;top:40px}
.products-head h2{font-size:25px;font-weight:700}
.products-head p{font-size:12px;margin-top:4px}
.view-all{position:absolute;right:57px;top:36px;background:#fff;color:var(--primary);font-size:13px}
.cards{position:absolute;left:57px;top:118px;display:flex;gap:14px}
.card{width:261px;height:501px;background:#fff;color:var(--ink);text-align:center;position:relative}
.card-img{height:260px;position:relative}
.card h3{font-size:14px;font-weight:600;margin-top:24px;text-transform:uppercase}
.card h3.accent{color:var(--primary)}
.card p{font-size:12.5px;line-height:19.5px;color:var(--muted);padding:0 20px;margin-top:16px}
.card .btn{position:absolute;left:40px;right:40px;bottom:24px;text-align:center}

/* why */
.why{height:654px;position:relative}
.why h2{position:absolute;top:50px;width:100%;text-align:center}
.feature{position:absolute;width:534px;height:221px;border:1px solid var(--line);display:flex}
.feature-img{width:260px;height:100%;position:relative;flex:none}
.feature-body{padding:22px 18px}
.feature h3{font-size:14px;line-height:17px;font-weight:600;color:var(--primary);text-transform:uppercase}
.feature p{font-size:12.5px;line-height:19.5px;color:var(--muted);margin-top:12px}

/* process */
.process{height:626px;background:var(--mint);position:relative}
.process h2{position:absolute;top:40px;width:100%;text-align:center}
.step{position:absolute;top:101px;width:338px}
.step-img{height:337px;position:relative}
.step-head{display:flex;align-items:center;gap:12px;margin-top:24px}
.step-num{width:34px;height:34px;border-radius:50%;background:var(--teal);color:#fff;font-family:"Archivo",sans-serif;font-size:13px;font-weight:600;display:flex;align-items:center;justify-content:center}
.step h3{font-size:13.5px;font-weight:600;color:var(--primary);text-transform:uppercase}
.step p{font-size:12.5px;line-height:20px;color:var(--muted);margin-top:12px}

/* projects */
.projects{height:460px;position:relative}
.projects h2{position:absolute;left:57px;top:40px}
.arrows{position:absolute;right:57px;top:43px;display:flex;gap:8px}
.arrow{width:29px;height:29px;display:flex;align-items:center;justify-content:center;border:1.5px solid var(--primary)}
.arrow.on{background:var(--primary)}
.project{position:absolute;top:104px;width:262px;height:333px;overflow:hidden}
.pin{position:absolute;left:16px;top:20px;background:var(--primary);color:#fff;font-family:"Archivo",sans-serif;font-size:11px;font-weight:600;padding:4px 9px 4px 5px;display:flex;align-items:center;gap:6px;border-radius:2px}
.pin i{width:14px;height:14px;border-radius:50%;background:#fff;display:block;position:relative}
.pin i::after{content:"";position:absolute;left:4.5px;top:4.5px;width:5px;height:5px;border-radius:50%;background:var(--primary)}
.project-name{position:absolute;left:0;right:0;bottom:0;height:48px;background:var(--primary);color:#fff;font-family:"Archivo",sans-serif;font-size:13px;font-weight:600;display:flex;align-items:center;justify-content:center}
.project-tag{position:absolute;left:16px;right:16px;bottom:16px;height:30px;display:flex}
.project-tag span{flex:1;background:#fff;color:var(--primary);font-family:"Archivo",sans-serif;font-size:13px;font-weight:600;display:flex;align-items:center;justify-content:center;white-space:nowrap}
.project-tag b{width:30px;background:var(--teal);display:flex;align-items:center;justify-content:center}

/* serving */
.serving{height:325px;position:relative}
.serving-text{position:absolute;left:57px;top:98px;width:490px}
.serving-text p{font-size:12.5px;line-height:20px;color:var(--muted);margin-top:14px}
.map{position:absolute;left:639px;top:21px;width:505px;height:262px;background:linear-gradient(135deg,#cfe3c9 0%,#e4ecd9 45%,#d8e5ee 100%)}

/* contact */
.contact{height:427px;background:var(--mint);position:relative}
.contact-info{position:absolute;left:57px;top:48px;width:480px}
.license{font-size:11.5px;color:var(--muted);margin-top:10px}
.contact-info p.lead{font-size:12.5px;line-height:20px;color:var(--muted);margin-top:14px}
.info-row{display:flex;align-items:center;gap:16px;font-size:14px;font-weight:600;line-height:20px}
.icon-circle{width:34px;height:34px;border-radius:50%;background:var(--primary);display:flex;align-items:center;justify-content:center;flex:none}
.contact-form{position:absolute;left:608px;top:36px;width:536px}
.contact-form h2{text-align:center;font-size:25px;line-height:30px}
.field{background:#fff;border:1px solid var(--line);border-radius:19px;height:38px;font-size:12px;color:#8a8a8a;padding:0 16px;display:flex;align-items:center}
.row{display:flex;gap:12px;margin-top:11px}
.row .field{flex:1}
.message{height:115px;border-radius:14px;align-items:flex-start;padding-top:16px;margin-top:11px}
.send{margin-top:21px;height:40px;border-radius:20px;background:var(--primary);color:#fff;font-family:"Archivo",sans-serif;font-size:13px;font-weight:600;display:flex;align-items:center;justify-content:center}

/* footer */
.site-footer{height:263px;background:var(--footer);position:relative;color:#fff}
.footer-brand{position:absolute;left:57px;top:30px;display:flex;align-items:center;gap:14px}
.footer-brand .brand-mark{width:52px;height:52px;background:var(--sky)}
.footer-brand .brand-name{color:var(--cyan-light);font-size:27px;line-height:30px;font-weight:500}
.footer-about{position:absolute;left:57px;top:126px;width:340px;font-size:12.5px;line-height:20px}
.footer-col{position:absolute;top:45px}
.footer-col h3{font-size:12.5px;font-weight:500;color:var(--cyan-light);text-transform:uppercase}
.footer-col ul{list-style:none;margin-top:12px}
.footer-col li{font-size:12.5px;line-height:30px;display:flex;align-items:center;gap:12px}
.footer-col li::before{content:"";width:5px;height:5px;background:var(--teal-light);transform:rotate(45deg)}
.socials{display:flex;gap:12px;margin-top:14px}
.socials span{width:29px;height:29px;border-radius:50%;background:var(--sky);display:block}
.footer-rule{position:absolute;left:0;right:0;top:216px;border-top:1px solid #34486a}
.copyright{position:absolute;left:0;right:0;top:233px;text-align:center;font-size:12.5px}
</style>
</head>
<body>

<header class="site-header">
  <div class="brand"><span class="brand-mark"></span><span class="brand-name">COPPERLEAF<br>BALUSTRADE</span></div>
  <nav class="nav">
    <a class="active" href="#">HOME</a><a href="#">ABOUT</a><a href="#">PRODUCT</a><a href="#">WHY CHOOSE US</a><a class="cta" href="#">CONTACT</a>
  </nav>
</header>

<section class="hero">
  <div class="ph" role="img" aria-label="Woman on a wooden deck with railings overlooking green hills at sunset"></div>
  <div class="hero-content">
    <h1>Elevate your outdoor spaces<br>with stunning railings</h1>
    <p>Serving homeowners, builders, and commercial developers across the Washington State, we specialize in crafting custom railing systems designed to withstand the region's unique climate while enhancing the beauty of your outdoor living spaces.</p>
    <div class="actions"><a class="btn btn-solid" href="#">Learn More</a><a class="btn btn-ghost" href="#">Contact Us</a></div>
  </div>
  <div class="hero-next"><svg width="20" height="12" viewBox="0 0 20 12"><path d="M1 6h17M13 1l5 5-5 5" stroke="#fff" stroke-width="1.6" fill="none"/></svg></div>
</section>

<section class="about">
  <div class="about-photo" role="img" aria-label="Rooftop deck with black metal railing overlooking a valley town and pine trees"></div>
  <div class="about-text">
    <h2 class="section-title">About</h2>
    <p>At Copperleaf Balustrade, we believe that every outdoor space deserves the perfect blend of style, safety, and durability. Serving homeowners, builders, and commercial developers across the Washington State, we specialize in crafting custom railing systems designed to withstand the region's unique climate while enhancing the beauty of your outdoor living spaces.</p>
    <p>With a focus on premium materials, expert craftsmanship, and exceptional customer service, Copperleaf Balustrade is proud to be the trusted partner for both residential and commercial railing projects. Whether you're looking to complement a new deck, add a modern touch to your balcony, or create a secure and stunning barrier for a commercial space, we've got the perfect solution for you.</p>
    <a class="btn btn-solid" href="#">Learn More</a>
  </div>
</section>

<section class="products">
  <div class="ph" role="img" aria-label="Dark forest background"></div>
  <div class="products-head">
    <h2>OUR PRODUCT</h2>
    <p>We offer a wide variety of custom and railing systems designed to meet the needs of every project</p>
  </div>
  <a class="btn view-all" href="#">View All</a>
  <div class="cards">
    <article class="card">
      <div class="card-img" role="img" aria-label="Hand on a bronze aluminum handrail" style="background:linear-gradient(160deg,#9aa78a,#5f6b47 60%,#3d4530)"></div>
      <h3 class="accent">Aluminum Railings</h3>
      <p>A Sleek, low-maintenance option, our powder-coated aluminum railings provide strength, corrosion resistance, and a modern aesthetic. Available in a range of colors and finishes.</p>
      <a class="btn btn-solid" href="#">Read More</a>
    </article>
    <article class="card">
      <div class="card-img" role="img" aria-label="Glass stair railing under a clear sky" style="background:linear-gradient(180deg,#a9d1d3,#6fa7ad 55%,#2f3a3b)"></div>
      <h3>Glass Railings</h3>
      <p>Ideal for breathtaking views and clean lines, our glass railings combine tempered glass with sturdy framing to create an elegant, transparent barrier that maintains the beauty of your surroundings.</p>
      <a class="btn btn-outline" href="#">Read More</a>
    </article>
    <article class="card">
      <div class="card-img" role="img" aria-label="Wooden staircase with steel cable railing" style="background:linear-gradient(180deg,#e9e8e4,#c9b49a 55%,#8a5a35)"></div>
      <h3>Cable Railings</h3>
      <p>Our stainless steel cable railing systems offer an unobstructed view, ideal for homes or businesses with scenic landscapes. The minimalist design ensures safety while preserving sightlines</p>
      <a class="btn btn-outline" href="#">Read More</a>
    </article>
    <article class="card">
      <div class="card-img" role="img" aria-label="Modern house balcony with custom glass railing" style="background:linear-gradient(180deg,#cfd8de,#7c878e 55%,#3b4147)"></div>
      <h3>Custom Design</h3>
      <p>If we don't have exactly what you're looking for, we can customize your vision or source additional manufacturers to find exactly what you're looking for.</p>
      <a class="btn btn-outline" href="#">Read More</a>
    </article>
  </div>
</section>

<section class="why">
  <h2 class="section-title">Why choose Copperleaf Balustrade ?</h2>
  <div class="feature" style="left:57px;top:128px">
    <div class="feature-img" role="img" aria-label="Black metal railing against a red house wall" style="background:linear-gradient(135deg,#8c2a2a,#3d3d3d 55%,#6a6a6a)"></div>
    <div class="feature-body"><h3>Locally Crafted,<br>Regionally Resilient</h3><p>Our railings are designed with the Pacific Northwest's weather in mind—rain, snow, and everything in between. We use durable materials that are resistant to corrosion, moisture, and the elements, ensuring your railings stand the test of time</p></div>
  </div>
  <div class="feature" style="left:610px;top:128px">
    <div class="feature-img" role="img" aria-label="Wooden interior staircase with decorative iron balusters" style="background:linear-gradient(135deg,#e6e1d8,#a26a3a 55%,#5c3a1e)"></div>
    <div class="feature-body"><h3>Custom Solutions<br>for Every Need</h3><p>We work closely with you to design and fabricate custom railing systems that perfectly suit your space, style, and functional requirements. From intricate designs to minimalistic finishes, we tailor every project to your vision.</p></div>
  </div>
  <div class="feature" style="left:57px;top:377px">
    <div class="feature-img" role="img" aria-label="Black metal railing covered in snow with snowy trees" style="background:linear-gradient(135deg,#eef1f3,#9aa3a8 55%,#2e3438)"></div>
    <div class="feature-body"><h3>Expert Installation &amp;<br>Craftsmanship</h3><p>Our skilled craftsmen take pride in delivering exceptional workmanship, while our professional installers ensure every railing is securely mounted and aligned to meet local safety codes.</p></div>
  </div>
  <div class="feature" style="left:610px;top:377px">
    <div class="feature-img" role="img" aria-label="Timber house porch with black railing among trees" style="background:linear-gradient(135deg,#5a7a4a,#8a5a35 55%,#2a2a2a)"></div>
    <div class="feature-body" style="padding-top:30px"><h3>Full-Service Partner</h3><p>From the initial consultation and design process to installation and ongoing maintenance, we are with you every step of the way to ensure your project exceeds expectations.</p></div>
  </div>
</section>

<section class="process">
  <h2 class="section-title">Our Process</h2>
  <div class="step" style="left:57px">
    <div class="step-img" role="img" aria-label="Hands sketching architectural floor plans with a calculator" style="background:linear-gradient(135deg,#e9e3d6,#f3f1ec 50%,#c9b89a)"></div>
    <div class="step-head"><span class="step-num">01</span><h3>Consultation &amp; Design</h3></div>
    <p>We start by listening to your vision and understanding your specific needs. Our team will offer expert advice and design ideas to help you choose the best materials and styles.</p>
  </div>
  <div class="step" style="left:431px">
    <div class="step-img" role="img" aria-label="Two installers fitting glass railing panels on a balcony" style="background:linear-gradient(180deg,#6a8f62,#3a5a8a 55%,#6fc2a0)"></div>
    <div class="step-head"><span class="step-num">02</span><h3>Professional Installation</h3></div>
    <p>Our experienced team handles all aspects of installation, from measuring to securing, ensuring your railing is safe, secure, and perfectly aligned.</p>
  </div>
  <div class="step" style="left:806px">
    <div class="step-img" role="img" aria-label="Worker installing a cable railing post on deck stairs" style="background:linear-gradient(135deg,#c9cdd0,#8a5a3a 55%,#5a3a22)"></div>
    <div class="step-head"><span class="step-num">03</span><h3>Ongoing Support</h3></div>
    <p>We offer warranties on all of our products and services, and we are always available to help with maintenance or modifications down the road.</p>
  </div>
</section>

<section class="projects">
  <h2 class="section-title">Project Highlights</h2>
  <div class="arrows">
    <span class="arrow on"><svg width="14" height="10" viewBox="0 0 14 10"><path d="M13 5H1M5 1L1 5l4 4" stroke="#fff" stroke-width="1.4" fill="none"/></svg></span>
    <span class="arrow"><svg width="14" height="10" viewBox="0 0 14 10"><path d="M1 5h12M9 1l4 4-4 4" stroke="#0054AA" stroke-width="1.4" fill="none"/></svg></span>
  </div>
  <div class="project" style="left:57px">
    <div class="ph" role="img" aria-label="Timber deck with black railing overlooking a snowy forest" style="background:linear-gradient(180deg,#5a3a22,#c9ced2 45%,#e9ecee 70%,#2a2a2a)"></div>
    <span class="pin"><i></i>CLE ELUM, WA</span>
    <div class="project-name">RIDGELINE CUSTOM HOME</div>
  </div>
  <div class="project" style="left:332px">
    <div class="ph" role="img" aria-label="Grey modern house with glass balcony railing" style="background:linear-gradient(180deg,#dfe3e6,#5a5e62 50%,#2e3134)"></div>
    <span class="pin"><i></i>YAKIMA, WA</span>
    <div class="project-tag"><span>SCENIC VIEW HOME</span><b><svg width="12" height="12" viewBox="0 0 12 12"><path d="M2 10L10 2M4 2h6v6" stroke="#fff" stroke-width="1.3" fill="none"/></svg></b></div>
  </div>
  <div class="project" style="left:608px">
    <div class="ph" role="img" aria-label="Clubhouse balcony with horizontal black railing" style="background:linear-gradient(180deg,#c9cdd0,#6a6e70 50%,#3a3c3e)"></div>
    <span class="pin"><i></i>YAKIMA, WA</span>
    <div class="project-tag"><span>ORCHARD GOLF COURSE</span><b><svg width="12" height="12" viewBox="0 0 12 12"><path d="M2 10L10 2M4 2h6v6" stroke="#fff" stroke-width="1.3" fill="none"/></svg></b></div>
  </div>
  <div class="project" style="left:882px">
    <div class="ph" role="img" aria-label="Private residence with glass deck railing" style="background:linear-gradient(180deg,#e3e6e8,#7a7e82 50%,#3c3f42)"></div>
    <span class="pin"><i></i>YAKIMA, WA</span>
    <div class="project-tag"><span>PRIVATE RESIDENCE</span><b><svg width="12" height="12" viewBox="0 0 12 12"><path d="M2 10L10 2M4 2h6v6" stroke="#fff" stroke-width="1.3" fill="none"/></svg></b></div>
  </div>
</section>

<section class="serving">
  <div class="serving-text">
    <h2 class="section-title">Serving Washington State</h2>
    <p>Copperleaf Balustrade is proud to serve the entire state of Washington. Whether you're upgrading your home's deck or outfitting a commercial space, we understand the importance of creating beautiful, durable railings that stand up to the region's diverse and often challenging weather conditions.</p>
  </div>
  <div class="map" role="img" aria-label="Map of Washington State with a location pin near Yakima"></div>
</section>

<section class="contact">
  <div class="contact-info">
    <h2 class="section-title">Contact Us Today</h2>
    <p class="license">WA GC LICENSE # COPPEBL417QA</p>
    <p class="lead">Ready to elevate your space with a custom railing solution that's built to last? Reach out to the Copperleaf Balustrade team for a free consultation. Let us bring your vision to life with craftsmanship, care, and precision.</p>
    <div class="info-row" style="margin-top:40px"><span class="icon-circle"><svg width="16" height="16" viewBox="0 0 24 24"><path d="M6.6 10.8a15 15 0 006.6 6.6l2.2-2.2c.3-.3.7-.4 1-.2 1.1.4 2.3.6 3.6.6.6 0 1 .4 1 1V20c0 .6-.4 1-1 1A17 17 0 013 4c0-.6.4-1 1-1h3.5c.6 0 1 .4 1 1 0 1.3.2 2.5.6 3.6.1.3 0 .7-.2 1z" fill="#fff"/></svg></span>(509) 555-0142</div>
    <div class="info-row" style="margin-top:24px"><span class="icon-circle"><svg width="14" height="18" viewBox="0 0 14 18"><path d="M7 0a7 7 0 017 7c0 5-7 11-7 11S0 12 0 7a7 7 0 017-7z" fill="#fff"/><circle cx="7" cy="7" r="2.6" fill="#0054AA"/></svg></span><span>1480 Cedar Hollow Rd<br>Yakima, WA 98901</span></div>
    <div class="info-row" style="margin-top:24px"><span class="icon-circle"><svg width="18" height="18" viewBox="0 0 20 20" fill="none" stroke="#fff" stroke-width="1.4"><circle cx="10" cy="10" r="8"/><ellipse cx="10" cy="10" rx="3.5" ry="8"/><path d="M2 10h16"/></svg></span>www.copperleafbalustrade-example.com</div>
  </div>
  <div class="contact-form">
    <h2 class="section-title">Let's build your dream<br>outdoor space together</h2>
    <div class="row" style="margin-top:22px"><div class="field">Your Name</div><div class="field">Last Name</div></div>
    <div class="row"><div class="field">E - Mail</div><div class="field">Subject</div></div>
    <div class="field message">Message...</div>
    <div class="send">SEND MESSAGE</div>
  </div>
</section>

<footer class="site-footer">
  <div class="footer-brand"><span class="brand-mark"></span><span class="brand-name">COPPERLEAF<br>BALUSTRADE</span></div>
  <p class="footer-about">we specialize in crafting custom railing systems designed to withstand the region's unique climate while enhancing the beauty of your outdoor spaces.</p>
  <div class="footer-col" style="left:504px"><h3>Quick Links</h3><ul><li>Home</li><li>Product</li><li>Why Choose us</li><li>Contact</li></ul></div>
  <div class="footer-col" style="left:726px"><h3>Our Product</h3><ul><li>Aluminum Railings</li><li>Glass Railings</li><li>Cable Railings</li><li>Custom design</li></ul></div>
  <div class="footer-col" style="left:985px"><h3>Connect With Us</h3><div class="socials" aria-label="Social media links"><span></span><span></span><span></span><span></span></div></div>
  <div class="footer-rule"></div>
  <p class="copyright">© Copyright 2024 &nbsp;All Rights Reserved</p>
</footer>

</body>
</html>
```